Willow Cradle Pregnancy and Baby Massage

I need a web design for a new business, WILLOW CRADLE PREGNANCY AND BABY MASSAGE that I am in the process of setting up in the suburbs of Perth, Western Australia. The business is owned and operated by myself and my intention is to service Pregnant Mothers and Parents of Young Babies that would benefit from massage. I would like to have a "Home Page" and pages for "About Me", "Pregnancy Massage", "Baby Massage", a Pricing Page for Pregnancy Massage Sessions, a Pricing Page for Baby Massage Sessions, and a "Contact Me" page to allow clients to either contact me with queries or book available pregnancy massage sessions on a particular day of the week. I would also like a "News" page that would include articles I have written, news about new courses and a link to my Facebook page (yet to be set up). I would like to keep the colour schemes similar to my logo design colours. I need the design to be easy to follow and to appeal to a younger audience (20's to mid 30's).
The target audience is pregnant mothers-to-be wishing to receive massage treatments, and new parents and grandparents of small babies that would like to learn how to massage their babies.
The look and feel should be modern, professional, elegant and feminine.
I need the design to be in a standard format such that I can update the content by myself ( and does not need specialised software) as the company and business progresses.

Target Market(s)

Contact Information for Business Card

Card should have rounded edges. Design should have the same "feel" as the website. Contact Details of my business address, mobile phone, email and website should be included.

Font styles to use
Script

Requirements
Must have
• Same colours as logo design. In cmyk system, the colours are: 20,60,0,0 which best result is pantone 681 and 40,40,0,0 which best result is pantone 2645. Card should include the logo design.

```html
<!DOCTYPE html>
<html lang="en">
<head>
<meta charset="utf-8">
<title>Willow Cradle Pregnancy and Baby Massage</title>
<link rel="stylesheet" href="https://fonts.googleapis.com/css2?family=Open+Sans:wght@400;600&family=Dancing+Script:wght@700&display=swap">
<style>
:root{
  --pink:#b86ea3;
  --lavender:#8d84b9;
  --frame:#f1e6e8;
  --frame-edge:#d9cbcf;
  --ink:#222;
  --grey:#8a8a8a;
  --rule:#d4d4d4;
  --white:#fff;
}
*{box-sizing:border-box;margin:0;padding:0}
html,body{width:885px;height:1200px;overflow:hidden;background:var(--white)}
body{position:relative;font-family:"Open Sans",sans-serif;color:var(--ink)}
.site-header{position:absolute;left:0;top:0;width:885px;height:76px;border-top:2px solid var(--pink);background:var(--white);z-index:3}
.main-nav a{position:absolute;top:33px;font-size:12px;color:var(--ink);text-decoration:none}
.header-wave{position:absolute;left:0;top:74px;z-index:3}
.brand{position:absolute;left:372px;top:6px;width:140px;text-align:center;z-index:4;color:var(--pink)}
.brand-dot{width:28px;height:28px;border-radius:50%;background:var(--pink);margin:0 auto 4px}
.brand-name{font-size:16px;font-weight:600;line-height:1.05}
.brand-sub{font-size:9px;font-weight:600;line-height:1.4}
.hero{position:absolute;left:0;top:76px;width:885px;height:379px;background:linear-gradient(100deg,#6c6a70 0%,#b49bc6 30%,#c4b3cf 45%,#d8d1cf 65%,#9a9aa0 85%,#c9c6c8 100%)}
.hero-title{position:absolute;left:70px;top:95px;font-family:"Dancing Script",cursive;font-size:42px;line-height:52px;color:var(--white)}
.hero-dots{position:absolute;left:73px;top:220px;display:flex;gap:3px}
.hero-dots span{width:13px;height:13px;border-radius:50%;border:1.5px solid var(--white)}
.hero-dots span.active{background:var(--pink)}
.card{position:absolute;width:349px;background:var(--frame);border:1px solid var(--frame-edge);border-radius:5px;box-shadow:0 1px 3px rgba(0,0,0,.25);padding:6px}
.card-photo{height:205px;border-radius:2px}
.photo-a{background:radial-gradient(circle at 60% 50%,#e9d4c4 0%,#c98878 35%,#8e6570 75%,#6f5563 100%)}
.photo-b{background:radial-gradient(circle at 50% 55%,#e6c2b0 0%,#b08474 35%,#6e5a4c 70%,#c9a986 100%)}
.card-text{height:100%;display:flex;flex-direction:column;justify-content:center;gap:8px;color:var(--white);font-size:11px;line-height:1.55;text-align:center;padding:0 10px}
.badge{position:absolute;width:52px;height:52px;border-radius:50%;border:4px solid var(--frame);box-shadow:0 1px 3px rgba(0,0,0,.3)}
.connector{position:absolute;width:0;border-left:1px dashed var(--pink);height:50px}
.footer-rule{position:absolute;left:72px;top:1070px;width:741px;border-top:1.5px solid var(--rule)}
.cert{position:absolute;left:74px;top:1097px;display:flex;gap:8px}
.cert-mark{width:62px;height:82px;border:1.5px solid var(--pink);border-radius:4px}
.cert-text{font-size:13px;line-height:17px;color:var(--grey);font-weight:400}
.cert-text em{font-style:normal;color:var(--pink)}
.copyright{position:absolute;right:72px;top:1111px;font-size:10.5px}
.social{position:absolute;right:72px;top:1148px;display:flex;gap:7px}
.social span{width:23px;height:23px;border-radius:50%;border:2px solid #cfd8e4}
</style>
</head>
<body>
<header class="site-header">
  <nav class="main-nav">
    <a href="#" style="left:72px">Home</a>
    <a href="#" style="left:143px">About Me</a>
    <a href="#" style="left:234px">Pregnancy Massage</a>
    <a href="#" style="left:533px">Baby Massage</a>
    <a href="#" style="left:635px">Pricing</a>
    <a href="#" style="left:696px">News</a>
    <a href="#" style="left:750px">Contact Me</a>
  </nav>
</header>
<svg class="header-wave" width="885" height="32" viewBox="0 0 885 32">
  <path d="M330 0 C380 0 400 28 442 28 C484 28 504 0 555 0 Z" fill="#fff" stroke="#c9c9c9" stroke-width="1"/>
  <rect x="320" y="-2" width="245" height="3" fill="#fff"/>
</svg>
<div class="brand">
  <div class="brand-dot"></div>
  <div class="brand-name">Willow Cradle</div>
  <div class="brand-sub">Pregnancy and Baby Massage</div>
</div>

<section class="hero" role="img" aria-label="Pregnant woman relaxing on her side while a therapist massages her shoulder">
  <h1 class="hero-title">Willow Cradle Pregnancy<br>&amp; Baby Massage</h1>
  <div class="hero-dots"><span class="active"></span><span></span><span></span><span></span><span></span></div>
</section>

<div class="card" style="left:72px;top:509px"><div class="card-photo photo-a" role="img" aria-label="Newborn twins wrapped in coral cloth on a heart-shaped lace backdrop"></div></div>
<div class="card" style="left:463px;top:509px"><div class="card-photo photo-b" role="img" aria-label="Newborn twins cuddled together in a fur-lined basket"></div></div>

<div class="badge" style="left:221px;top:702px;background:var(--pink)"></div>
<div class="badge" style="left:612px;top:702px;background:var(--lavender)"></div>
<div class="connector" style="left:247px;top:755px"></div>
<div class="connector" style="left:638px;top:755px"></div>

<div class="card" style="left:72px;top:805px;height:156px">
  <div class="card-text" style="background:var(--pink)">
    <p>Willow Cradle Pregnancy and Baby Massage was launched in 2017, offering massage for pregnant women, and instruction of baby massage to parents, grandparents and carers.</p>
  </div>
</div>
<div class="card" style="left:463px;top:805px;height:213px">
  <div class="card-text" style="background:var(--lavender)">
    <p>My vision is to provide a professional massage service to pregnant mothers and babies that also benefits from my skills and experience as a midwife</p>
    <p>My expectation is that after each session, my clients should leave feeling relaxed, calm, emotionally nurtured, soothed and supported.</p>
    <p>At all times, I will take the utmost care of your privacy, safety and comfort in what is a very personal, intimate time in your life.</p>
  </div>
</div>

<footer>
  <div class="footer-rule"></div>
  <div class="cert">
    <div class="cert-mark"></div>
    <div class="cert-text">Certified by<br><em>tender touch</em><br><em>massage</em><br>guild</div>
  </div>
  <p class="copyright">Copyrights @ 2017 Willow Cradle Pregnancy &amp; Baby Massage. All Rights Reserved.</p>
  <div class="social"><span style="background:#3b5a9a"></span><span style="background:#1a83b8"></span><span style="background:#2aa3e0"></span><span style="background:#d2412c"></span></div>
</footer>
</body>
</html>
```